Coastal Learner Bureau business cards

Australian company about to start offering its services. We recruit international students to come to study English, vocational education and postgraduate courses in Australia. We help them find the institution and select the right city they want to come to Australia. We are a young, online oriented and supportive agency. Our clients are between 18 and 35 years old, mainly University students, young professionals or people with work experience. We provide much more information that any other agency offer. We administrate a Facebook group with more than 11.000 members that daily ask questions about general information when coming to Australia, while they are here and even after they leave the country

Target Market(s)

International students from South America, Central America and Europe

Industry/Entity Type

Student

Contact Information for Business Card

Tomas Bilbrea
Managing Director
tomas@kelvarin.com.au
www.kelvoria.com.au
+61 491058264
Melbourne, Australia

Font styles to use
Serif
Sans Serif

Colors

Designer to choose colors to be used in the design.

Requirements
Must have
• Horizontal design
• Standard business card size and shape. If font uses green or yellow colours, they will have to match the ones from the logo
Nice to have
• UPDATE: Use the contents of the green image to design one of the card sides. Use our logo in the background of that side as watermark.
• Passport image, or immigration stamps. A picture of the Yarra River (from Melbourne) would be cool as well.
Should not have
• Non-standard business card size and shape
• Not black as the background colour of any sides as we are not a VIP agency or a hight class service. We are orientes to young people and they like colours, pictures, something attractive.
• Vertical design
• NO YELLOW or BLACK AS THE BACKGROUND COLOUR OF ANY SIDE OF THE BIZ CARD

```html
<!DOCTYPE html>
<html lang="en">
<head>
<meta charset="utf-8">
<title>Coastal Learner Bureau – Business Cards</title>
<link href="https://fonts.googleapis.com/css2?family=Roboto+Condensed:wght@500;700&family=Roboto:wght@400;500;700&display=swap" rel="stylesheet">
<style>
  :root {
    --bg: #3a3a3a;
    --paper: #f2f2f2;
    --green: #115c3d;
    --yellow: #e0b11a;
    --ink: #444444;
    --white: #ffffff;
  }
  * { margin: 0; padding: 0; box-sizing: border-box; }
  html, body { width: 1200px; height: 960px; overflow: hidden; }
  body { background: var(--bg); font-family: "Roboto", Arial, sans-serif; position: relative; }

  .card { position: absolute; width: 600px; height: 343px; overflow: hidden; }
  .card--front { left: 314px; top: 113px; background: var(--paper); }
  .card--back { left: 311px; top: 472px; background: var(--green); }

  .front__band { position: absolute; left: 0; top: 43px; width: 600px; height: 116px; }
  .front__identity { position: absolute; left: 38px; top: 80px; }
  .front__name {
    font-family: "Roboto Condensed", Arial, sans-serif; font-weight: 700;
    font-size: 23px; color: var(--yellow); letter-spacing: 0.2px; line-height: 1;
  }
  .front__title {
    font-family: "Roboto Condensed", Arial, sans-serif; font-weight: 500;
    font-size: 17px; color: var(--white); margin-top: 5px; line-height: 1;
  }

  .brand-name {
    font-family: "Roboto", Arial, sans-serif; font-weight: 700; line-height: 1.05;
  }
  .front__brand {
    position: absolute; left: 468px; top: 62px; width: 118px;
    font-size: 24px; color: var(--green);
    background: var(--paper); padding: 14px 10px; border-radius: 4px;
  }

  .contact-list { position: absolute; left: 38px; top: 255px; list-style: none; }
  .contact-list li {
    display: flex; align-items: center; gap: 7px;
    font-size: 15px; color: var(--ink); height: 19.5px;
  }
  .contact-list svg { width: 13px; height: 13px; fill: var(--green); flex: none; }

  .front__location {
    position: absolute; right: 36px; top: 291px;
    display: flex; align-items: center; gap: 5px; font-size: 15px; color: var(--ink);
  }
  .front__location svg { width: 12px; height: 17px; fill: var(--green); }

  .back__brand {
    position: absolute; left: 0; right: 0; top: 122px;
    text-align: center; font-size: 40px; color: var(--white);
  }
  .back__tagline {
    position: absolute; left: 62px; right: 62px; top: 299px;
    display: flex; align-items: center; gap: 4px;
    font-size: 15px; color: var(--white); white-space: nowrap;
  }
  .back__tagline .rule { flex: 1; height: 1px; }
  .back__tagline .rule--left { background: linear-gradient(to right, transparent, rgba(255,255,255,0.8)); }
  .back__tagline .rule--right { background: linear-gradient(to left, transparent, rgba(255,255,255,0.8)); }
</style>
</head>
<body>

<section class="card card--front" aria-label="Business card front">
  <svg class="front__band" viewBox="0 0 600 116" aria-hidden="true">
    <polygon points="0,0 425,0 470,116 0,116" fill="var(--green)"/>
  </svg>
  <div class="front__identity">
    <p class="front__name">TOMAS BILBREA</p>
    <p class="front__title">MANAGING DIRECTOR</p>
  </div>
  <p class="front__brand brand-name">Coastal Learner Bureau</p>

  <ul class="contact-list">
    <li>
      <svg viewBox="0 0 24 24" aria-hidden="true"><path d="M6.6 10.8a15.1 15.1 0 0 0 6.6 6.6l2.2-2.2a1 1 0 0 1 1-.25 11.4 11.4 0 0 0 3.6.57 1 1 0 0 1 1 1V20a1 1 0 0 1-1 1A17 17 0 0 1 3 4a1 1 0 0 1 1-1h3.5a1 1 0 0 1 1 1c0 1.25.2 2.45.57 3.57a1 1 0 0 1-.25 1z"/></svg>
      +61 491058264
    </li>
    <li>
      <svg viewBox="0 0 24 24" aria-hidden="true"><path d="M2 5h20v2l-10 6L2 7zm0 4.3 10 6 10-6V19H2z"/></svg>
      tomas@kelvarin.com.au
    </li>
    <li>
      <svg viewBox="0 0 24 24" aria-hidden="true"><circle cx="12" cy="12" r="10"/><path d="M2 12h20M12 2c3 3 3 17 0 20M12 2c-3 3-3 17 0 20" stroke="var(--paper)" stroke-width="1.6" fill="none"/></svg>
      www.kelvoria.com.au
    </li>
  </ul>

  <p class="front__location">
    Melbourne, Australia
    <svg viewBox="0 0 24 34" aria-hidden="true"><path d="M12 0A12 12 0 0 0 0 12c0 9 12 22 12 22s12-13 12-22A12 12 0 0 0 12 0zm0 17a5 5 0 1 1 0-10 5 5 0 0 1 0 10z"/></svg>
  </p>
</section>

<section class="card card--back" aria-label="Business card back">
  <p class="back__brand brand-name">Coastal Learner Bureau</p>
  <p class="back__tagline">
    <span class="rule rule--left"></span>
    Hacemos más por ti!
    <span class="rule rule--right"></span>
  </p>
</section>

</body>
</html>
```